Power Point Template

I would like to have a power point template for our company.
See our website: www.brekkavikfjord.se for logo/colors and inspiration.

The template will be used for bank meetings etc, so it should be formal and professional.

Should show examples of various layouts.
Updates

I want the following headings/sections/example slides: - Slide with table of contents - Slide with bullets (just to show how a bullet list looks like) - Slide with project timeline - Slide with business case calculations (table e.g.) - slide with pictures with room for descriptive text (to show inspirational pictures, one slide per section: exterior, interior upper floor, exterior lower floor)? - Slide where our buildings are described (bullet list) - Slide with presentation of our business partners - First page with a faded background picture of our building (the one where our logo is shown)

Industry/Entity Type

It Company

```html
<!DOCTYPE html>
<html lang="en">
<head>
<meta charset="utf-8">
<title>Our Bullet – brekkavikfjord</title>
<link href="https://fonts.googleapis.com/css2?family=Roboto+Condensed:wght@400;700&display=swap" rel="stylesheet">
<style>
  :root {
    --page-bg: #f7f7f7;
    --navy: #0f3a6e;
    --ink: #111111;
    --body-text: #2f2f2f;
    --accent: #fbb03b;
    --footer-band: #9ea5ae;
  }
  html, body {
    margin: 0;
    padding: 0;
    overflow: hidden;
  }
  body {
    width: 1200px;
    height: 900px;
    background: var(--page-bg);
    font-family: "Roboto Condensed", "Arial Narrow", sans-serif;
  }
  .slide {
    position: relative;
    width: 1200px;
    height: 900px;
    overflow: hidden;
    background: var(--page-bg);
  }
  .brand {
    position: absolute;
    top: 30px;
    right: 18px;
    display: flex;
    align-items: center;
    gap: 10px;
    font-size: 26px;
    font-weight: 700;
    color: var(--navy);
  }
  .brand-square {
    width: 16px;
    height: 16px;
    background: var(--accent);
  }
  .slide-title {
    position: absolute;
    top: 72px;
    left: 0;
    width: 1200px;
    margin: 0;
    text-align: center;
    font-size: 38px;
    font-weight: 400;
    color: var(--ink);
    line-height: 1;
  }
  .slide-title strong { font-weight: 700; }
  .title-rule {
    position: absolute;
    top: 122px;
    left: 396px;
    width: 408px;
    height: 4px;
    background: var(--accent);
  }
  .bullet-list {
    list-style: none;
    margin: 0;
    padding: 0;
  }
  .bullet-item {
    position: absolute;
    left: 43px;
    width: 1075px;
  }
  .bullet-item:nth-child(1) { top: 192px; }
  .bullet-item:nth-child(2) { top: 389px; }
  .bullet-item:nth-child(3) { top: 600px; }
  .bullet-marker {
    position: absolute;
    left: 0;
    top: 4px;
    width: 28px;
    height: 28px;
    background: var(--navy);
  }
  .bullet-heading {
    margin: 0 0 8px 56px;
    font-size: 27px;
    font-weight: 700;
    color: var(--navy);
    line-height: 36px;
  }
  .bullet-text {
    margin: 0 0 0 56px;
    font-size: 20px;
    line-height: 31.5px;
    color: var(--body-text);
    text-align: justify;
  }
  .footer-band {
    position: absolute;
    left: 0;
    bottom: 0;
    width: 1200px;
    height: 27px;
    background: var(--footer-band);
  }
</style>
</head>
<body>
<div class="slide">
  <div class="brand"><span class="brand-square"></span>brekkavikfjord</div>

  <h1 class="slide-title">OUR <strong>BULLET</strong></h1>
  <div class="title-rule"></div>

  <ul class="bullet-list">
    <li class="bullet-item">
      <span class="bullet-marker"></span>
      <h2 class="bullet-heading">Bullet Poiint Here</h2>
      <p class="bullet-text">Lorem Ipsum is simply dummy text of the printing and typesetting industry. Lorem Ipsum has been the industry's standard dummy text&nbsp; Lorem Ipsum is simply dummy text of the printing and typesetting industry. Lorem Ipsum has been the industry's standard dummy text Lorem Ipsum is simply dummy text of the printing and typ</p>
    </li>
    <li class="bullet-item">
      <span class="bullet-marker"></span>
      <h2 class="bullet-heading">Bullet Poiint Here</h2>
      <p class="bullet-text">Lorem Ipsum is simply dummy text of the printing and typesetting industry. Lorem Ipsum has been the industry's standard dummy text&nbsp; Lorem Ipsum is simply dummy text of the printing and typesetting industry. Lorem Ipsum has been the industry's standard dummy text Lorem Ipsum is simply dummy text of the printing and typ</p>
    </li>
    <li class="bullet-item">
      <span class="bullet-marker"></span>
      <h2 class="bullet-heading">Bullet Poiint Here</h2>
      <p class="bullet-text">Lorem Ipsum is simply dummy text of the printing and typesetting industry. Lorem Ipsum has been the industry's standard dummy text&nbsp; Lorem Ipsum is simply dummy text of the printing and typesetting industry. Lorem Ipsum has been the industry's standard dummy text Lorem Ipsum is simply dummy text of the printing and typ</p>
    </li>
  </ul>

  <div class="footer-band"></div>
</div>
</body>
</html>
```